Brell Stone Company Business Cards

Front and Back Business Card - logo and text setup - cool design. I need workable photoshop or illustrator files so I can setup each employee card with design that is created
Updates

Hi everyone, thank you for the great entries. Please no more white and blue cards - there are so many already - black and silver only now please. thanks!

Target Market(s)

Construction Industry - Facility Managers

Industry/Entity Type

Construction

Contact Information for Business Card

I really like contemporary simplistic looks - clean neat....not opposed to seeing some black backrounds

Requirements
Must have
• Logo/website address with design on front only - www.brellstone-example.com (logo attached)
• Back:
• Name/Title/Company Address/Phone/email address
Nice to have
• Cool design
Should not have
• Nothing gimmicky like Fire or Water - since we are a Fire Protection company - it has all been done

```html
<!DOCTYPE html>
<html lang="en">
<head>
<meta charset="utf-8">
<title>Brell Stone Company Business Card</title>
<link href="https://fonts.googleapis.com/css2?family=Montserrat:wght@400;500;800&display=swap" rel="stylesheet">
<style>
  :root {
    --black: #141416;
    --black-soft: #202024;
    --silver: #c9cbcf;
    --silver-light: #e9eaec;
    --silver-dark: #8e9196;
    --ink-light: #d6d8dc;
    --backdrop: #5a5c60;
  }
  html, body {
    margin: 0;
    width: 1200px;
    height: 900px;
    overflow: hidden;
    background: var(--backdrop);
    font-family: "Montserrat", sans-serif;
  }
  .canvas {
    position: relative;
    width: 1200px;
    height: 900px;
  }
  .card {
    position: absolute;
    left: 250px;
    width: 700px;
    height: 400px;
    overflow: hidden;
    box-shadow: 0 10px 30px rgba(0,0,0,0.45);
  }
  .card--details { top: 35px; background: var(--black); }
  .card--brand { top: 465px; background: linear-gradient(135deg, var(--black), var(--black-soft)); }
  .card-art { position: absolute; inset: 0; }
  .contact-block {
    position: absolute;
    left: 46px;
    top: 70px;
    color: var(--ink-light);
    font-size: 14px;
    line-height: 1.6;
  }
  .contact-name {
    margin: 0;
    color: var(--silver-light);
    font-size: 24px;
    font-weight: 500;
    letter-spacing: 0.5px;
    white-space: nowrap;
  }
  .contact-title { margin: 0 0 14px; font-size: 14px; color: var(--silver-dark); }
  .contact-address { margin: 0 0 14px; }
  .contact-list { list-style: none; margin: 0; padding: 0; }
  .contact-list li { display: flex; align-items: center; gap: 10px; white-space: nowrap; }
  .contact-icon { width: 12px; height: 12px; flex: none; }
  .brand-mark {
    position: absolute;
    display: flex;
    align-items: center;
    gap: 12px;
    font-weight: 800;
    letter-spacing: -0.5px;
    white-space: nowrap;
  }
  .brand-mark--light { left: 450px; top: 158px; color: var(--black); font-size: 34px; }
  .brand-mark--dark { left: 50%; top: 50%; transform: translate(-50%, -50%); color: var(--silver); font-size: 64px; }
  .brand-square { width: 0.4em; height: 0.4em; flex: none; }
  .brand-mark--light .brand-square { background: var(--silver-dark); }
  .brand-mark--dark .brand-square { background: var(--silver-light); }
</style>
</head>
<body>
<main class="canvas">
  <section class="card card--details" aria-label="Business card, contact side">
    <svg class="card-art" width="700" height="400" viewBox="0 0 700 400" aria-hidden="true">
      <defs>
        <linearGradient id="panel-sheen" x1="0" y1="0" x2="1" y2="1">
          <stop offset="0" stop-color="#eeeff1"/>
          <stop offset="1" stop-color="#c4c6ca"/>
        </linearGradient>
      </defs>
      <path d="M390 0 C310 120 322 300 500 400 L700 400 L700 0 Z" fill="url(#panel-sheen)"/>
      <path d="M376 0 C296 120 308 300 486 400" fill="none" stroke="#8e9196" stroke-width="6"/>
    </svg>
    <div class="contact-block">
      <h1 class="contact-name">DANIEL ROWE</h1>
      <p class="contact-title">Director</p>
      <p class="contact-address">48 Harbor Lane<br>Westfield, NY 11900</p>
      <ul class="contact-list">
        <li><svg class="contact-icon" viewBox="0 0 12 12"><path d="M2 1 L4.5 1 L5.5 3.5 L4 4.8 C4.8 6.6 5.6 7.4 7.2 8 L8.5 6.5 L11 7.5 L11 10 C6 11 1 6 2 1 Z" fill="#c9cbcf"/></svg>(555) 201-4470</li>
        <li><svg class="contact-icon" viewBox="0 0 12 12"><rect x="1" y="2" width="10" height="8" rx="1" fill="#c9cbcf"/></svg>(555) 201-4471</li>
        <li><svg class="contact-icon" viewBox="0 0 12 12"><rect x="1" y="2.5" width="10" height="7" fill="none" stroke="#c9cbcf" stroke-width="1.4"/><path d="M1 2.5 L6 7 L11 2.5" fill="none" stroke="#c9cbcf" stroke-width="1.4"/></svg>info@brellstone-example.com</li>
        <li><svg class="contact-icon" viewBox="0 0 12 12"><circle cx="6" cy="6" r="5" fill="none" stroke="#c9cbcf" stroke-width="1.4"/><path d="M1 6 H11 M6 1 C3 4 3 8 6 11 C9 8 9 4 6 1" fill="none" stroke="#c9cbcf" stroke-width="1"/></svg>www.brellstone-example.com</li>
      </ul>
    </div>
    <div class="brand-mark brand-mark--light"><span class="brand-square"></span>Brell Stone</div>
  </section>

  <section class="card card--brand" aria-label="Business card, brand side">
    <div class="brand-mark brand-mark--dark"><span class="brand-square"></span>Brell Stone</div>
  </section>
</main>
</body>
</html>
```